sydney wedding photography business needs a business card design

we need a business card design for a sydney based wedding photography and videography business. our business name is :golden hour studio and film. our target clients are 24-35 yrs female. our style is candid, organic, natural, dynamic. we are a team of young photographers and videographers, and help brides to create memories that they will cherish for the rest of their lives. the logo will be provided. we want an elegant design that reflects our style, and also want to give a great impression to our clients that we are one of the best studios in sydney and our brand means quality and premium service.

Target Market(s)

bride to be, 24-35 years old, living in sydney and surrunding areas

Industry/Entity Type

Wedding Photography

Contact Information for Business Card

address: 57 tarrant street, glenmore nsw 2047
mobile: 0431872259
phone: (02) 9163 2408
info@tidewillowstudio.net.au
www.tidewillowstudio.net.au
facebook:tidewillowweddings
instagram:tidewillowweddings

Font styles to use
Serif
Sans Serif

Requirements
Nice to have
• maybe add my slogan"memories beyond eternity" if the layout looks good
Should not have
• no black color, not good idea for wedding biz card

```html
<!DOCTYPE html>
<html lang="en">
<head>
<meta charset="utf-8">
<title>Golden Hour Studio and Film – Business Card</title>
<link href="https://fonts.googleapis.com/css2?family=Source+Sans+3:wght@400;600&display=swap" rel="stylesheet">
<style>
  :root {
    --backdrop: #cdc5bb;
    --card: #f5eee3;
    --card-edge: #e4d9c8;
    --gold: #a87a1e;
    --ink-strong: #4a4038;
    --ink-muted: #877b6e;
    --rule: #c9b99f;
  }
  * { box-sizing: border-box; margin: 0; padding: 0; }
  html, body {
    width: 1200px; height: 864px; overflow: hidden;
    background: var(--backdrop);
    font-family: "Source Sans 3", "Helvetica Neue", Arial, sans-serif;
  }
  .canvas { position: relative; width: 1200px; height: 864px; }

  .card {
    position: absolute; width: 525px; height: 300px;
    background: var(--card);
    border: 1px solid var(--card-edge);
    border-radius: 4px;
    box-shadow: 0 10px 28px rgba(60,45,30,.22);
  }

  /* front */
  .card--front { left: 70px; top: 110px; }
  .front-mark {
    position: absolute; left: 0; right: 0; top: 78px;
    display: flex; flex-direction: column; align-items: center; gap: 14px;
  }
  .front-mark__dot {
    width: 18px; height: 18px; border-radius: 50%; background: var(--gold);
  }
  .front-mark__name {
    color: var(--gold); font-weight: 600; font-size: 22px; letter-spacing: 1px;
  }
  .front-social {
    position: absolute; left: 40px; right: 40px; top: 196px;
  }
  .front-social__rule {
    position: relative; height: 1px; background: var(--rule);
  }
  .front-social__dot {
    position: absolute; left: 50%; top: -6px; width: 12px; height: 12px;
    margin-left: -6px; border-radius: 50%; background: var(--ink-muted);
  }
  .front-social__handle {
    margin-top: 14px; text-align: center;
    color: var(--ink-muted); font-size: 15px; letter-spacing: .4px;
  }

  /* back */
  .card--back { left: 605px; top: 450px; }
  .brand-name {
    position: absolute; right: 34px; top: 46px;
    color: var(--gold); font-weight: 600; font-size: 24px; letter-spacing: .5px;
    text-align: right;
  }
  .person {
    position: absolute; left: 34px; top: 138px; width: 170px; text-align: right;
  }
  .person__name { color: var(--gold); font-size: 19px; font-weight: 600; }
  .person__role { color: var(--ink-strong); font-size: 16px; margin-top: 2px; }
  .person__address { color: var(--ink-muted); font-size: 13px; margin-top: 8px; line-height: 1.35; }
  .divider {
    position: absolute; left: 222px; top: 140px; width: 1px; height: 112px;
    background: var(--rule);
  }
  .contact {
    position: absolute; left: 240px; top: 140px; list-style: none;
  }
  .contact__row {
    display: flex; align-items: center; gap: 9px;
    color: var(--ink-strong); font-size: 14px; height: 27px;
  }
  .contact__icon { width: 14px; height: 14px; fill: var(--gold); flex: none; }
  .contact__icon .cut { fill: var(--card); }
  .contact__icon .cut-line { fill: none; stroke: var(--card); }
</style>
</head>
<body>
<main class="canvas">

  <section class="card card--front" aria-label="Card front">
    <div class="front-mark">
      <span class="front-mark__dot"></span>
      <span class="front-mark__name">Golden Hour Studio and Film</span>
    </div>
    <div class="front-social">
      <div class="front-social__rule"><span class="front-social__dot"></span></div>
      <p class="front-social__handle">tidewillowweddings</p>
    </div>
  </section>

  <section class="card card--back" aria-label="Card back">
    <p class="brand-name">Golden Hour Studio and Film</p>

    <div class="person">
      <p class="person__name">Mara Ellison</p>
      <p class="person__role">President</p>
      <p class="person__address">57 tarrant street<br>glenmore nsw 2047</p>
    </div>

    <span class="divider"></span>

    <ul class="contact">
      <li class="contact__row">
        <svg class="contact__icon" viewBox="0 0 16 16" aria-hidden="true"><path d="M1 5c0-2 2-3 7-3s7 1 7 3v1h-4V4.5H5V6H1z"/><path d="M3 7h10l1 7H2z"/><circle class="cut" cx="8" cy="10.5" r="1.8"/></svg>
        <span>(02) 9163 2408</span>
      </li>
      <li class="contact__row">
        <svg class="contact__icon" viewBox="0 0 16 16" aria-hidden="true"><path d="M4 1h8a1 1 0 0 1 1 1v12a1 1 0 0 1-1 1H4a1 1 0 0 1-1-1V2a1 1 0 0 1 1-1zm1 2v9h6V3z"/></svg>
        <span>(04) 3187 2259</span>
      </li>
      <li class="contact__row">
        <svg class="contact__icon" viewBox="0 0 16 16" aria-hidden="true"><path d="M1 3h14v10H1z"/><path class="cut-line" d="M1 3l7 6 7-6" stroke-width="1.4"/></svg>
        <span>info@tidewillowstudio.net.au</span>
      </li>
      <li class="contact__row">
        <svg class="contact__icon" viewBox="0 0 16 16" aria-hidden="true"><circle cx="8" cy="8" r="7"/><path class="cut-line" d="M1 8h14M8 1c-3 3-3 11 0 14M8 1c3 3 3 11 0 14" stroke-width="1.1"/></svg>
        <span>www.tidewillowstudio.net.au</span>
      </li>
    </ul>
  </section>

</main>
</body>
</html>
```